I need a new business card designed, we recently rebranded and I need to get a fresh design to match our new logo, colours and branding.

Details:

Derek Havill | Founder & CEO
Address: 7 Marlowfern Lane, #09-14 Tavenport Crest, Singapore 318547
Tel: +65 93568214
Web: www.frostkarta.com.sg
hello@frostkarta.com.sg

I've attached my old card as well

Industry/Entity Type

Business

Requirements
Must have
• Front and Back
Interesting use of logo
Correct use of colour scheme

```html
<!DOCTYPE html>
<html lang="en">
<head>
<meta charset="utf-8">
<title>Frostkarta business card – front and back</title>
<link rel="stylesheet" href="https://fonts.googleapis.com/css2?family=Arimo:wght@400;700&display=swap">
<style>
  :root {
    --stage: #000000;
    --label: #8a8a8a;
    --card-top: #ffffff;
    --card-bottom: #ececed;
    --ink: #000000;
    --brand-name: #7d6e66;
    --title-blue: #4fc0ee;
    --contact-blue: #1f8ad0;
    --bar-start: #2aa7e0;
    --bar-end: #8ad6f8;
    --block-sky: #5cc2ef;
    --block-blue: #2ea6de;
    --block-taupe: #a89a90;
    --block-brown: #76665c;
  }
  * { margin: 0; padding: 0; box-sizing: border-box; }
  html, body { width: 1200px; height: 1000px; overflow: hidden; background: var(--stage); }
  .stage { position: relative; width: 1200px; height: 1000px; font-family: "Arimo", Arial, sans-serif; }
  .side-label { position: absolute; left: 164px; font-size: 24px; color: var(--label); line-height: 1; }
  .side-label--front { top: 97px; }
  .side-label--back { top: 561px; }

  .card { position: absolute; overflow: hidden; background: linear-gradient(180deg, var(--card-top) 10%, var(--card-bottom) 100%); }
  .card--front { left: 257px; top: 82px; width: 698px; height: 402px; }
  .card--back { left: 256px; top: 545px; width: 697px; height: 399px; }

  .brand-name { position: absolute; font-weight: 700; color: var(--brand-name); line-height: 1; letter-spacing: -0.5px; }
  .card--front .brand-name { left: 42px; top: 58px; font-size: 42px; }
  .card--back .brand-name { left: 0; width: 100%; text-align: center; top: 181px; font-size: 36px; }

  .person { position: absolute; left: 55px; top: 184px; }
  .person__name { font-size: 38px; font-weight: 700; color: var(--ink); line-height: 1; }
  .person__title { font-size: 20px; font-weight: 700; color: var(--title-blue); line-height: 1; margin-top: 4px; }

  .contact { position: absolute; left: 372px; top: 145px; font-size: 18px; color: var(--contact-blue); line-height: 31px; }
  .contact__row { display: flex; }
  .contact__row--gap { margin-top: 30px; }
  .contact__label { width: 77px; }
  .contact__sep { width: 22px; }
  .contact__address { display: flex; flex-direction: column; }

  .accent-bar { position: absolute; left: 0; bottom: 0; width: 100%; height: 23px; display: flex; }
  .accent-bar__fade { width: 508px; background: linear-gradient(90deg, var(--bar-start), var(--bar-end)); }
  .accent-bar__block { width: 47.5px; }
  .accent-bar__block--sky { background: var(--block-sky); }
  .accent-bar__block--blue { background: var(--block-blue); }
  .accent-bar__block--taupe { background: var(--block-taupe); }
  .accent-bar__block--brown { background: var(--block-brown); }
</style>
</head>
<body>
<main class="stage">
  <p class="side-label side-label--front">Front</p>
  <section class="card card--front" aria-label="Card front">
    <p class="brand-name">frostkarta</p>
    <div class="person">
      <h1 class="person__name">Derek Havill</h1>
      <p class="person__title">Founder &amp; CEO</p>
    </div>
    <div class="contact">
      <div class="contact__row"><span class="contact__label">Tel</span><span class="contact__sep">:</span><span>+65 93568214</span></div>
      <div class="contact__row"><span class="contact__label">Web</span><span class="contact__sep">:</span><span>www.frostkarta.com.sg</span></div>
      <div class="contact__row"><span class="contact__label">e-mail</span><span class="contact__sep">:</span><span>hello@frostkarta.com.sg</span></div>
      <div class="contact__row contact__row--gap"><span class="contact__label">Address</span><span class="contact__sep">:</span>
        <span class="contact__address"><span>7 Marlowfern Lane,</span><span>#09-14 Tavenport Crest,</span><span>Singapore 318547</span></span>
      </div>
    </div>
    <div class="accent-bar">
      <span class="accent-bar__fade"></span>
      <span class="accent-bar__block accent-bar__block--sky"></span>
      <span class="accent-bar__block accent-bar__block--blue"></span>
      <span class="accent-bar__block accent-bar__block--taupe"></span>
      <span class="accent-bar__block accent-bar__block--brown"></span>
    </div>
  </section>

  <p class="side-label side-label--back">Back</p>
  <section class="card card--back" aria-label="Card back">
    <p class="brand-name">frostkarta</p>
  </section>
</main>
</body>
</html>
```